Harborview Estates Business Card for Apartment Buildings

Create business cards for resident managers who run apartment buildings. The audience is the public who are searching for apartment rentals, and current residents who live at the apartment building. Key design element will be incorporating the company logo, however, the logo cannot dominate. The building name and manager name are more important than the logo. Current business card design leaves little room for copy, so we may need to reduce the size on the current card to allow for more space for copy.

Target Market(s)

Adults 18-65 years of age, who are looking for an apartment rental, plus current residents who live at our apartment buildings.

Industry/Entity Type

Property Management

Contact Information for Business Card

A major design element will be use of the company logo. Important property and manager contact information must be part of the design. The size of the logo will need to be reduced to make room for building and manager contact copy.

Font styles to use
Sans Serif

Colors
3176b5
000000
959595
ffffff

Requirements
Must have
• 1) Incorporate the company logo.
• 2) Use the company colors (dark blue, black/grey, over white).
• 3) FEATURE THE BUILDING NAME
• 4) FEATURE THE MANAGER NAME
• 5) The company name is less important than BUILDING and MANAGER
• 6) Manager contact information
• **SEE ATTACHED CREATIVE BRIEF**
Nice to have
• 1) Back of card logo watermark
• 2) Ability to write notes on back of carfd
Should not have
• Avoid letting the company logo dominate the card, the building name and manager are more important than the company logo.

```html
<!DOCTYPE html>
<html lang="en">
<head>
<meta charset="utf-8">
<title>Harborview Estates – Business Card</title>
<link href="https://fonts.googleapis.com/css2?family=Roboto:wght@400;500;700&family=Roboto+Condensed:wght@500&display=swap" rel="stylesheet">
<style>
  :root {
    --brand-blue: #3176b5;
    --ink: #333333;
    --text-grey: #555555;
    --mid-grey: #959595;
    --card: #f4f4f4;
    --backdrop: #2b2b2b;
    --watermark: rgba(149,149,149,0.16);
  }
  html, body {
    margin: 0;
    width: 1200px;
    height: 960px;
    overflow: hidden;
    background: var(--backdrop);
    font-family: "Roboto", Arial, sans-serif;
  }
  .card {
    position: absolute;
    width: 600px;
    height: 342px;
    background: var(--card);
    overflow: hidden;
    box-shadow: 0 2px 6px rgba(0,0,0,0.5);
  }
  .card--front { left: 314px; top: 113px; }
  .card--back  { left: 311px; top: 472px; }

  .watermark-ring {
    position: absolute;
    left: 296px;
    top: 6px;
    width: 420px;
    height: 420px;
    border-radius: 50%;
    background: var(--watermark);
  }

  .brand {
    position: absolute;
    display: flex;
    align-items: center;
    gap: 10px;
  }
  .brand__mark {
    background: var(--brand-blue);
    flex: none;
  }
  .brand__name {
    color: var(--brand-blue);
    font-weight: 700;
    letter-spacing: 0.5px;
    line-height: 1;
    white-space: nowrap;
  }
  .card--front .brand { left: 44px; top: 60px; }
  .card--front .brand__mark { width: 34px; height: 34px; }
  .card--front .brand__name { font-size: 22px; }

  .card--back .brand { left: 50%; top: 50%; transform: translate(-50%, -50%); gap: 14px; }
  .card--back .brand__mark { width: 56px; height: 56px; }
  .card--back .brand__name { font-size: 36px; }

  .property {
    position: absolute;
    left: 43px;
    top: 138px;
  }
  .property__name {
    margin: 0;
    font-size: 21px;
    font-weight: 500;
    color: var(--brand-blue);
    line-height: 26px;
  }
  .property__address {
    margin: 0;
    font-size: 14px;
    line-height: 19px;
    color: var(--text-grey);
    font-style: normal;
  }

  .contact-list {
    position: absolute;
    left: 43px;
    top: 216px;
    margin: 0;
    padding: 0;
    list-style: none;
  }
  .contact-list li {
    display: flex;
    align-items: center;
    gap: 8px;
    height: 19px;
    font-size: 14px;
    color: var(--text-grey);
  }
  .contact-list svg {
    width: 14px;
    height: 14px;
    fill: var(--brand-blue);
    flex: none;
  }

  .manager {
    position: absolute;
    right: 41px;
    top: 203px;
    text-align: right;
  }
  .manager__name {
    margin: 0;
    font-family: "Roboto Condensed", "Roboto", sans-serif;
    font-weight: 500;
    font-size: 23px;
    line-height: 26px;
    color: var(--brand-blue);
  }
  .manager__title {
    margin: 0;
    font-size: 15px;
    font-weight: 500;
    line-height: 20px;
    color: var(--ink);
  }
</style>
</head>
<body>

<section class="card card--front" aria-label="Business card front">
  <div class="watermark-ring" aria-hidden="true"></div>

  <div class="brand">
    <span class="brand__mark" aria-hidden="true"></span>
    <span class="brand__name">HARBORVIEW ESTATES</span>
  </div>

  <div class="property">
    <h1 class="property__name">Cedar Court Apartments</h1>
    <address class="property__address">1482 Marigold Avenue<br>Bayside, CA 90417</address>
  </div>

  <ul class="contact-list">
    <li>
      <svg viewBox="0 0 16 16" aria-hidden="true"><path d="M3.6 1.2l2.3 2.6c.3.4.3.9 0 1.2L4.7 6.3c.9 2 2.6 3.8 4.9 4.9l1.3-1.2c.3-.3.9-.3 1.2 0l2.6 2.3c.4.3.4.9 0 1.3l-1.4 1.3c-.5.5-1.3.6-2 .4C6.5 13.8 2.2 9.5.7 4.7c-.2-.7-.1-1.5.4-2l1.3-1.4c.3-.4.9-.4 1.2-.1z"/></svg>
      555-210-4381
    </li>
    <li>
      <svg viewBox="0 0 16 16" aria-hidden="true"><path d="M4.5 0h7c.8 0 1.5.7 1.5 1.5v13c0 .8-.7 1.5-1.5 1.5h-7C3.7 16 3 15.3 3 14.5v-13C3 .7 3.7 0 4.5 0zM5 2v10.5h6V2H5zm3 11.3a.9.9 0 100 1.8.9.9 0 000-1.8z"/></svg>
      555-734-9062
    </li>
    <li>
      <svg viewBox="0 0 16 16" aria-hidden="true"><path d="M4 1h8v4H4zM1.5 6h13c.8 0 1.5.7 1.5 1.5V12h-3v3H3v-3H0V7.5C0 6.7.7 6 1.5 6zM4.5 10.5v3h7v-3z"/></svg>
      555-468-1175
    </li>
    <li>
      <svg viewBox="0 0 16 16" aria-hidden="true"><path d="M1 3h14v1.2L8 8.6 1 4.2zM1 5.6l7 4.4 7-4.4V13H1z"/></svg>
      lena@harborviewest.com
    </li>
    <li>
      <svg viewBox="0 0 16 16" aria-hidden="true"><path d="M8 .5a7.5 7.5 0 100 15 7.5 7.5 0 000-15zm-1 2.2c.8.6.4 1.7-.3 2.1-.9.5-.5 1.6.4 1.8 1 .2 1.8 1 1.4 2-.4.9-1.6 1-1.7 2.1-.1.9.4 1.9-.4 2.2A5.6 5.6 0 012.6 6c1 .1 1.7.9 2.5.5.7-.4.2-1.5.9-2.3.3-.4.7-.9 1-1.5zm3.6 1c1.4.9 2.4 2.5 2.4 4.3 0 .6-.1 1.1-.3 1.6-.5-.6-1.3-.8-1.7-1.5-.4-.8.3-1.8-.3-2.5-.4-.5-1.2-.3-1.4-.9-.2-.4.6-.8 1.3-1z"/></svg>
      www.harborviewest.com
    </li>
  </ul>

  <div class="manager">
    <h2 class="manager__name">Lena Morales</h2>
    <p class="manager__title">Resident Manager</p>
  </div>
</section>

<section class="card card--back" aria-label="Business card back">
  <div class="brand">
    <span class="brand__mark" aria-hidden="true"></span>
    <span class="brand__name">HARBORVIEW ESTATES</span>
  </div>
</section>

</body>
</html>
```